Business card design needed

I run a Beautician studio (for 7 years now)
I offer
- Velmo Body Sugaring
- Ruby Glaze
- Nails
- Facials
- Manicure
- Foot Treatment
It might not be necessary to list all those treatments?
Maybe the link to the Website is sufficient?
I leave that up to you ...
(more info on www.FernAndDewByLenka.com.au)
Velmo BodySugaring is our biggest success, It replaces waxing.
I would like to incorporate the logo into the Business Card.
We had many complaints regarding our old Business Cards as the Phone Number was to small.
On the backside, we would like a "your next Appointment" section.
Looking forward to you Design, cheers ... Lenka
Industry/Entity Type
Business
Contact Information for Business Card
Fern by Dew by Lenka
14 Korrin Sqr 3942 Marlowe
www.FernAndDewByLenka.com.au
03 9481 2267

```html
<!DOCTYPE html>
<html lang="en">
<head>
<meta charset="utf-8">
<title>Fern by Dew by Lenka – Business and Appointment Cards</title>
<link href="https://fonts.googleapis.com/css2?family=Arimo:wght@400;700&family=Cinzel:wght@500&family=Open+Sans:wght@400;600&display=swap" rel="stylesheet">
<style>
  :root {
    --backdrop: #1c1c1c;
    --card: #ffffff;
    --green: #0f9345;
    --ink: #1f1f1f;
    --grey: #555555;
    --orange: #e8581f;
    --amber: #f08a1d;
    --yellow: #f5c623;
    --rule: #9a9a9a;
  }
  * { box-sizing: border-box; margin: 0; padding: 0; }
  html, body { width: 1200px; height: 728px; overflow: hidden; }
  body { background: var(--backdrop); position: relative; font-family: "Arimo", Arial, sans-serif; color: var(--ink); }

  .card { position: absolute; width: 524px; height: 298px; background: var(--card); overflow: hidden; }
  .card--front { left: 41px; top: 37px; }
  .card--appointment { left: 597px; top: 37px; }
  .card--back { left: 43px; top: 368px; }
  .card--appointment-alt { left: 609px; top: 372px; }

  /* brand mark: plain circle + name */
  .brand { position: absolute; display: flex; flex-direction: column; align-items: center; text-align: center; }
  .brand__dot { width: 70px; height: 70px; border-radius: 50%; background: var(--amber); margin-bottom: 12px; }
  .brand__name { font-family: "Arimo", Arial, sans-serif; font-weight: 400; color: var(--ink); letter-spacing: 3px; text-transform: uppercase; line-height: 1.35; }

  .card--front .brand { left: 46px; top: 58px; width: 200px; }
  .card--front .brand__dot { width: 76px; height: 76px; margin-bottom: 14px; }
  .card--front .brand__name { font-size: 17px; }
  .divider { position: absolute; left: 258px; top: 33px; width: 1px; height: 168px; background: var(--rule); }
  .details { position: absolute; left: 270px; top: 37px; }
  .details__title { font-weight: 700; font-size: 20px; color: var(--green); }
  .details__address { font-size: 14px; margin-top: 2px; }
  .details__heading { font-weight: 700; font-size: 17px; color: var(--green); letter-spacing: 1px; margin-top: 10px; }
  .treatments { list-style: none; font-size: 14px; line-height: 20.5px; margin-top: 2px; }
  .treatments li::before { content: "\2022\00a0"; }
  .wave { position: absolute; left: 0; bottom: 0; width: 524px; height: 100px; }
  .contact { position: absolute; left: 70px; bottom: 9px; display: flex; gap: 18px; color: #fff; font-size: 14px; align-items: center; }
  .contact__item { display: flex; align-items: center; gap: 6px; }
  .contact__phone { font-size: 16px; }

  .card--back .brand { left: 0; right: 0; top: 30px; margin: 0 auto; width: 300px; }
  .card--back .brand__dot { width: 80px; height: 80px; margin-bottom: 22px; }
  .card--back .brand__name { font-size: 19px; line-height: 29px; }
  .back__web { position: absolute; top: 201px; width: 100%; text-align: center; font-family: "Open Sans", Arial, sans-serif; font-size: 14px; letter-spacing: 2.4px; color: var(--ink); }
  .back__hours-title { position: absolute; top: 234px; width: 100%; text-align: center; font-family: "Open Sans", Arial, sans-serif; font-weight: 600; font-size: 19px; letter-spacing: 1.5px; color: var(--grey); }
  .back__hours { position: absolute; top: 268px; width: 100%; text-align: center; font-family: "Open Sans", Arial, sans-serif; font-weight: 600; font-size: 14.5px; color: var(--grey); }
  .back__hours span { margin: 0 8px; color: var(--rule); font-weight: 400; }

  /* appointment cards */
  .appt { position: absolute; left: 33px; top: 52px; font-family: "Open Sans", Arial, sans-serif; font-size: 14.5px; color: #333; }
  .appt__title { font-family: "Cinzel", Georgia, serif; font-weight: 500; font-size: 18px; color: var(--green); letter-spacing: .5px; margin-bottom: 6px; }
  .appt__row { display: flex; align-items: center; height: 37px; }
  .appt__dotted { border-bottom: 1px dotted #888; height: 12px; }
  .appt__line { border-bottom: 1px solid #777; height: 12px; }
  .appt__box { width: 95px; height: 21px; border: 1px solid #666; margin-left: 10px; }
  .appt__box + .appt__box { margin-left: 30px; }
  .days { display: flex; align-items: center; font-weight: 600; color: #444; font-size: 14.5px; }
  .days__box { width: 34px; height: 21px; border: 1px solid #666; margin: 0 7px 0 8px; }
  .appt__note { font-size: 12.8px; line-height: 17px; margin-top: 18px; width: 458px; }
  .card--appointment .brand { left: 376px; top: 16px; width: 94px; }
  .card--appointment .brand__dot { width: 34px; height: 34px; margin-bottom: 6px; }
  .card--appointment .brand__name { font-size: 10.5px; letter-spacing: 1.5px; }
  .card--appointment-alt .appt { left: 31px; }
  .watermark { position: absolute; left: 95px; top: 18px; width: 330px; opacity: .08; }
  .watermark .brand__dot { width: 170px; height: 170px; }
  .watermark .brand__name { font-size: 30px; }
</style>
</head>
<body>

<section class="card card--front" aria-label="Business card front">
  <div class="brand">
    <div class="brand__dot"></div>
    <div class="brand__name">Velmo<br>Body Sugaring</div>
  </div>
  <div class="divider"></div>
  <div class="details">
    <h1 class="details__title">Fern by Dew by Lenka</h1>
    <p class="details__address">14 Korrin Sqr 3942 Marlowe</p>
    <h2 class="details__heading">Treatments offer</h2>
    <ul class="treatments">
      <li>Velmo Body Sugaring</li>
      <li>Ruby Glaze &bull; Nails</li>
      <li>Facials &bull; Manicure</li>
      <li>Foot Treatment</li>
    </ul>
  </div>
  <svg class="wave" viewBox="0 0 524 100" preserveAspectRatio="none" aria-hidden="true">
    <defs>
      <linearGradient id="bandGradient" x1="0" x2="1" y1="0" y2="0">
        <stop offset="0" stop-color="#e8581f"/>
        <stop offset=".5" stop-color="#f08a1d"/>
        <stop offset="1" stop-color="#f5c623"/>
      </linearGradient>
    </defs>
    <path d="M0 28 C130 48 200 76 300 68 C400 58 460 24 524 20 L524 100 L0 100 Z" fill="url(#bandGradient)"/>
    <path d="M0 20 C130 40 200 68 300 59 C400 50 460 16 524 13" fill="none" stroke="#0f9345" stroke-width="4"/>
  </svg>
  <div class="contact">
    <span class="contact__item contact__phone">
      <svg width="15" height="15" viewBox="0 0 24 24" aria-hidden="true"><path fill="#fff" d="M6.6 10.8a15.1 15.1 0 0 0 6.6 6.6l2.2-2.2c.3-.3.7-.4 1-.2 1.1.4 2.3.6 3.6.6.6 0 1 .4 1 1V20c0 .6-.4 1-1 1A17 17 0 0 1 3 4c0-.6.4-1 1-1h3.5c.6 0 1 .4 1 1 0 1.3.2 2.5.6 3.6.1.3 0 .7-.2 1z"/></svg>
      03 9481 2267
    </span>
    <span class="contact__item">
      <svg width="14" height="14" viewBox="0 0 24 24" aria-hidden="true" fill="none" stroke="#fff" stroke-width="2"><circle cx="12" cy="12" r="10"/><path d="M2 12h20M12 2c3 3 3 17 0 20M12 2c-3 3-3 17 0 20"/></svg>
      www.FernAndDewByLenka.com.au
    </span>
  </div>
</section>

<section class="card card--appointment" aria-label="Appointment card">
  <div class="brand">
    <div class="brand__dot"></div>
    <div class="brand__name">Velmo<br>Body Sugaring</div>
  </div>
  <div class="appt">
    <h2 class="appt__title">YOUR APPOINTMENT</h2>
    <div class="appt__row" style="height:26px">Name :<span class="appt__dotted" style="width:290px;margin-left:8px"></span></div>
    <div class="appt__row">Date :<span class="appt__line" style="width:96px;margin-left:18px"></span>&nbsp;&nbsp;Time :<span class="appt__line" style="width:90px;margin-left:4px"></span>am / pm</div>
    <div class="appt__row">Next Appointment<span class="appt__box"></span><span class="appt__box"></span></div>
    <div class="appt__row days">MON<span class="days__box"></span>TUE<span class="days__box"></span>WED<span class="days__box"></span>THU<span class="days__box"></span>FRI<span class="days__box"></span>SAT<span class="days__box"></span></div>
    <p class="appt__note">It would be appreciated if 24 hours notice could be given if you are unable to attend an appointment</p>
  </div>
</section>

<section class="card card--back" aria-label="Business card back">
  <div class="brand">
    <div class="brand__dot"></div>
    <div class="brand__name">Velmo<br>Body Sugaring</div>
  </div>
  <p class="back__web">www.FernAndDewByLenka.com.au</p>
  <h2 class="back__hours-title">Hours of Operation</h2>
  <p class="back__hours">Mon - Fri: 7.30am - 7.00pm<span>|</span>Saturday: 7.30am - 12.00pm</p>
</section>

<section class="card card--appointment-alt" aria-label="Appointment card, alternative">
  <div class="brand watermark" aria-hidden="true">
    <div class="brand__dot"></div>
    <div class="brand__name">Velmo Body Sugaring</div>
  </div>
  <div class="appt">
    <h2 class="appt__title">YOUR APPOINTMENT</h2>
    <div class="appt__row" style="height:26px">Name :<span class="appt__dotted" style="width:290px;margin-left:8px"></span></div>
    <div class="appt__row">Date :<span class="appt__line" style="width:96px;margin-left:18px"></span>&nbsp;&nbsp;Time :<span class="appt__line" style="width:90px;margin-left:4px"></span>am / pm</div>
    <div class="appt__row">Next Appointment<span class="appt__box"></span><span class="appt__box"></span></div>
    <div class="appt__row days">MON<span class="days__box"></span>TUE<span class="days__box"></span>WED<span class="days__box"></span>THU<span class="days__box"></span>FRI<span class="days__box"></span>SAT<span class="days__box"></span></div>
    <p class="appt__note">It would be appreciated if 24 hours notice could be given if you are unable to attend an appointment</p>
  </div>
</section>

</body>
</html>
```